Brisk Rainshield - Logo and Advert

Help to provide logo and advert.
Advert is to be short and concise to fit in a printed directory posted around homes.
Ideally the same advert to be able to be blown up as a leaflet.
Use of eco friendly type colours, soft greens and blues.
Logo to be subtle but indicative to roofing and facades.
Breakdown of advert as follows;
Company name:
Brisk Rainshield
Sub title:
Roofing & Façades
Services breakdown:
Pitched (Slating & Tiling)
Flat (Single Ply, Liquid & Mineral Felt)
Hard Metal (Zinc Standing Seam)
Leadwork
Roof lights and lanterns
Generic notes:
100% flame free applications available, eliminating all fire risks to your property. (No gas torch’s etc.).
Expert consultation and advice.
Product warranty and/or insurance backed warranty available.
Fully insured contractor.
Contact information:
Phone number to be confirmed
Email and/or website to be confirmed.
Please feel free to try out different colours and fonts other than outlined. I am not limited to those and open to suggestions.
Target Market(s)
Domestic/Private Home Owners/Small Buidlers
Industry/Entity Type
Roofing
Font styles to use
Look and feel
Each slider illustrates characteristics of the customer's brand and the style your logo design should communicate.

```html
<!DOCTYPE html>
<html lang="en">
<head>
<meta charset="utf-8">
<title>Brisk Rainshield – Roofing &amp; Façades Advert</title>
<link rel="stylesheet" href="https://fonts.googleapis.com/css2?family=Inter+Tight:wght@300;400;500;600;700;800&display=swap">
<style>
  :root {
    --sky-deep: #0a58bd;
    --sky: #2f8fe0;
    --sky-pale: #7db6e4;
    --roof-tan: #c79a70;
    --wall-white: #e8e6e1;
    --wall-grey: #bdb7ae;
    --ground: #9c7f66;
    --brand-blue: #0a90d1;
    --brand-green: #a6cd38;
    --ink: #3b3b3b;
    --white: #ffffff;
  }
  * { box-sizing: border-box; margin: 0; padding: 0; }
  html, body { width: 1009px; height: 1200px; overflow: hidden; background: var(--white); }
  body { font-family: "Inter Tight", "Helvetica Neue", Arial, sans-serif; }
  .advert { position: relative; width: 1009px; height: 1200px; overflow: hidden; background: var(--white); }

  .hero-photo {
    position: absolute; left: 0; top: 0; width: 1009px; height: 800px;
    background: linear-gradient(180deg,
      var(--sky-deep) 0%, var(--sky) 20%, var(--sky-pale) 29%,
      var(--roof-tan) 36%, #d8b08a 45%, #ddd3c6 52%,
      var(--wall-white) 62%, var(--wall-grey) 74%,
      #b59a80 86%, var(--ground) 100%);
  }
  .headline {
    position: absolute; left: 0; top: 60px; width: 1009px; text-align: center; color: var(--white);
    line-height: 1;
  }
  .headline-lead { display: block; font-weight: 300; font-size: 80px; letter-spacing: -3.6px; }
  .headline-main { display: block; font-weight: 800; font-size: 78px; letter-spacing: -3.6px; margin-top: 0; }

  .shapes { position: absolute; left: 0; top: 0; }

  .service { position: absolute; text-align: center; transform: translateX(-50%); line-height: 1.05; white-space: nowrap; }
  .service-name { font-weight: 700; font-size: 28px; letter-spacing: -1px; }
  .service-detail { font-weight: 600; font-size: 16px; letter-spacing: -0.6px; margin-top: 3px; }
  .is-green { color: var(--brand-green); }
  .is-blue { color: var(--brand-blue); }

  .promise-box {
    position: absolute; left: 110px; top: 865px; width: 790px; height: 154px;
    border: 1.5px solid var(--brand-blue); border-radius: 10px; overflow: hidden;
  }
  .flame-free {
    position: absolute; left: 0; top: 0; width: 393px; height: 100%;
    background: var(--brand-blue); color: var(--white);
    border-radius: 0 30px 30px 0 / 0 50% 50% 0;
    padding: 20px 0 0 36px;
  }
  .flame-free-title { font-weight: 700; font-size: 38px; letter-spacing: -2px; line-height: 1; margin-bottom: 6px; }
  .flame-free-text { font-weight: 400; font-size: 22px; letter-spacing: -1px; line-height: 26px; }
  .benefits { position: absolute; left: 430px; top: 24px; list-style: none; color: var(--ink); }
  .benefits li { position: relative; padding-left: 30px; font-size: 22px; letter-spacing: -1px; line-height: 23px; margin-bottom: 9px; }
  .benefits li svg { position: absolute; left: 2px; top: 6px; }

  .brand { position: absolute; left: 0; top: 1034px; width: 1009px; text-align: center; }
  .brand-name { font-weight: 400; font-size: 56px; letter-spacing: -2px; color: var(--brand-blue); line-height: 1; }
  .brand-tagline {
    display: flex; align-items: center; justify-content: center; gap: 10px; margin-top: 4px;
    font-weight: 400; font-size: 22px; letter-spacing: -0.4px; color: var(--brand-green);
  }
  .brand-tagline::before, .brand-tagline::after { content: ""; width: 105px; height: 1.5px; background: var(--brand-blue); }

  .contact-bar {
    position: absolute; left: 0; top: 1134px; width: 1009px; height: 66px; background: var(--brand-green);
    display: flex; align-items: center; justify-content: center; gap: 22px;
    color: var(--white); font-weight: 600; font-size: 25px; letter-spacing: -0.6px;
  }
  .contact-divider { font-weight: 400; }
</style>
</head>
<body>
<main class="advert">
  <div class="hero-photo" role="img" aria-label="Photo of a detached house under construction with scaffolding, timber gables and new roof tiles against a blue sky"></div>

  <h1 class="headline">
    <span class="headline-lead">THINKING ABOUT YOUR</span>
    <span class="headline-main">HOME IMPROVEMENT</span>
  </h1>

  <svg class="shapes" width="1009" height="1200" viewBox="0 0 1009 1200">
    <defs>
      <linearGradient id="leadTone" x1="0" y1="0" x2="1" y2="1"><stop offset="0" stop-color="#6f7579"/><stop offset="0.45" stop-color="#b8bdc1"/><stop offset="0.6" stop-color="#8d9397"/><stop offset="1" stop-color="#d3d7da"/></linearGradient>
      <linearGradient id="flatTone" x1="0" y1="0" x2="1" y2="1"><stop offset="0" stop-color="#ffffff"/><stop offset="0.4" stop-color="#d6e8f6"/><stop offset="0.55" stop-color="#6aa9dc"/><stop offset="1" stop-color="#3f86c6"/></linearGradient>
      <linearGradient id="lanternTone" x1="0" y1="0" x2="0" y2="1"><stop offset="0" stop-color="#2f7fd0"/><stop offset="0.35" stop-color="#9cc4e4"/><stop offset="0.55" stop-color="#6c8f6e"/><stop offset="0.75" stop-color="#4a535c"/><stop offset="1" stop-color="#262b30"/></linearGradient>
      <linearGradient id="slateTone" x1="0" y1="0" x2="0" y2="1"><stop offset="0" stop-color="#2f5a2c"/><stop offset="0.3" stop-color="#5f7d55"/><stop offset="0.4" stop-color="#8d969d"/><stop offset="0.85" stop-color="#a9b0b6"/><stop offset="1" stop-color="#e6e6e6"/></linearGradient>
      <linearGradient id="zincTone" x1="0" y1="0" x2="1" y2="0"><stop offset="0" stop-color="#5f656a"/><stop offset="0.5" stop-color="#7e8489"/><stop offset="1" stop-color="#9aa0a4"/></linearGradient>
    </defs>

    <path class="panel-curve" d="M0 761 Q504 560 1009 761 L1009 1200 L0 1200 Z" fill="#ffffff" stroke="#a6cd38" stroke-width="6"/>

    <g role="img" aria-label="Photo of a folded lead roof flashing">
      <circle cx="134" cy="694" r="108" fill="#a6cd38"/>
      <circle cx="134" cy="694" r="96" fill="url(#leadTone)"/>
    </g>
    <g role="img" aria-label="Photo of water droplets beading on a flat roof membrane">
      <circle cx="313" cy="644" r="108" fill="#0a90d1"/>
      <circle cx="313" cy="644" r="96" fill="url(#flatTone)"/>
    </g>
    <g role="img" aria-label="Photo of a glass roof lantern under a blue sky">
      <circle cx="503" cy="604" r="108" fill="#a6cd38"/>
      <circle cx="503" cy="604" r="96" fill="url(#lanternTone)"/>
    </g>
    <g role="img" aria-label="Photo of a pitched roof finished in grey slate tiles">
      <circle cx="694" cy="644" r="108" fill="#0a90d1"/>
      <circle cx="694" cy="644" r="96" fill="url(#slateTone)"/>
    </g>
    <g role="img" aria-label="Photo of zinc standing seam metal cladding">
      <circle cx="875" cy="694" r="108" fill="#a6cd38"/>
      <circle cx="875" cy="694" r="96" fill="url(#zincTone)"/>
    </g>
  </svg>

  <div class="service is-green" style="left:134px; top:805px;">
    <div class="service-name">Leadwork</div>
  </div>
  <div class="service is-blue" style="left:313px; top:754px;">
    <div class="service-name">Flat</div>
    <div class="service-detail">Single ply, Liquid<br>and Mineral felt</div>
  </div>
  <div class="service is-green" style="left:503px; top:717px;">
    <div class="service-name">Roof lights<br>and lanterns</div>
  </div>
  <div class="service is-blue" style="left:694px; top:754px;">
    <div class="service-name">Pitched</div>
    <div class="service-detail">Slating and Tiling</div>
  </div>
  <div class="service is-green" style="left:875px; top:805px;">
    <div class="service-name">Hard Metal</div>
    <div class="service-detail">Zinc Standing seam</div>
  </div>

  <section class="promise-box">
    <div class="flame-free">
      <p class="flame-free-title">100% Flame Free</p>
      <p class="flame-free-text">applications available, eliminating<br>all fire risks to your property.<br>(No gas torch’s etc).</p>
    </div>
    <ul class="benefits">
      <li><svg width="8" height="12" viewBox="0 0 8 12"><path d="M1 1l5 5-5 5" fill="none" stroke="#0a90d1" stroke-width="1.6"/></svg>Product warranty or insurance<br>backed warranty available.</li>
      <li><svg width="8" height="12" viewBox="0 0 8 12"><path d="M1 1l5 5-5 5" fill="none" stroke="#0a90d1" stroke-width="1.6"/></svg>Expert consultation and advice.</li>
      <li><svg width="8" height="12" viewBox="0 0 8 12"><path d="M1 1l5 5-5 5" fill="none" stroke="#0a90d1" stroke-width="1.6"/></svg>Fully insured contractor.</li>
    </ul>
  </section>

  <div class="brand">
    <p class="brand-name">BRISK RAINSHIELD</p>
    <p class="brand-tagline">ROOFING &amp; FAÇADES</p>
  </div>

  <footer class="contact-bar">
    <span>briskrainshield.co.uk</span>
    <span class="contact-divider">|</span>
    <span>hello@briskrainshield.co.uk</span>
    <span class="contact-divider">|</span>
    <span>0300 555 0142</span>
  </footer>
</main>
</body>
</html>
```